Harrow Grading LLC business card design

Excavation company business cards

Contact Information for Business Card

Harrow Grading LLC cell phone 208-417-6290 office phone 208-319-4856 harrowgradingllc@maplecove.com Driveways, site prep, retaining walls, septic systems, rock delivery

Colors

Designer to choose colors to be used in the design.

```html
<!DOCTYPE html>
<html lang="en">
<head>
<meta charset="utf-8">
<title>Harrow Grading LLC – Business Card</title>
<link href="https://fonts.googleapis.com/css2?family=Roboto:wght@400;700&display=swap" rel="stylesheet">
<style>
  :root {
    --backdrop: #bdbdbd;
    --card-white: #ffffff;
    --card-grey: #636363;
    --ink: #333333;
    --orange: #f06a1d;
    --edge-grey: #5a5a5a;
    --rule: #8a8a8a;
  }
  * { box-sizing: border-box; margin: 0; padding: 0; }
  html, body {
    width: 1200px; height: 788px; overflow: hidden;
    background: var(--backdrop);
    font-family: "Roboto", Arial, sans-serif;
  }
  .stage {
    position: relative; width: 1200px; height: 788px;
    display: flex; align-items: center; justify-content: center; gap: 50px;
  }
  .card {
    position: relative; width: 520px; height: 297px;
    border-radius: 18px; overflow: hidden;
  }
  /* Front */
  .card--front { background: var(--card-white); }
  .edge-accent {
    position: absolute; width: 60px; height: 10px;
    background: var(--edge-grey);
  }
  .edge-accent--top-right { top: 0; right: 0; }
  .edge-accent--bottom-left { bottom: 0; left: 0; }
  .orange-band {
    position: absolute; right: 0; bottom: 0; height: 10px; width: 460px;
    background: var(--orange);
  }
  .brand {
    position: absolute; left: 34px; top: 104px;
    display: flex; align-items: center; gap: 10px;
    white-space: nowrap;
  }
  .brand__mark { width: 16px; height: 16px; background: var(--orange); flex: none; }
  .brand__name {
    font-weight: 700; font-size: 24px; line-height: 1.1;
    color: var(--orange); letter-spacing: 0.3px;
  }
  .person {
    position: absolute; right: 32px; top: 34px; text-align: right;
  }
  .person__name {
    font-weight: 700; font-size: 22px; color: var(--orange);
    letter-spacing: 0.5px; text-transform: uppercase;
  }
  .person__rule {
    height: 1px; width: 240px; background: var(--rule); margin: 4px 0 3px auto;
  }
  .person__title { font-size: 14px; color: var(--ink); }
  .divider {
    position: absolute; left: 34px; top: 168px; width: 300px; height: 1px;
    background: var(--rule);
  }
  .contacts {
    position: absolute; left: 34px; top: 180px; list-style: none;
  }
  .contacts li {
    display: flex; align-items: center; gap: 8px;
    font-size: 14px; line-height: 21px; color: var(--ink);
    white-space: nowrap;
  }
  .contacts svg { width: 11px; height: 11px; flex: none; }
  /* Back */
  .card--back {
    background: var(--card-grey);
    display: flex; align-items: center; justify-content: center;
  }
  .back-brand { display: flex; align-items: center; gap: 14px; white-space: nowrap; }
  .back-brand__mark { width: 22px; height: 22px; background: var(--card-white); }
  .back-brand__name {
    font-weight: 700; font-size: 34px; color: var(--card-white); letter-spacing: 1px;
  }
</style>
</head>
<body>
<main class="stage">
  <section class="card card--front" aria-label="Front of business card">
    <div class="edge-accent edge-accent--top-right" role="img" aria-label="Grey edge accent band"></div>
    <div class="edge-accent edge-accent--bottom-left" role="img" aria-label="Grey edge accent band"></div>
    <div class="orange-band"></div>

    <div class="brand">
      <span class="brand__mark"></span>
      <span class="brand__name">Harrow Grading LLC</span>
    </div>

    <div class="person">
      <div class="person__name">Dalton Reyes</div>
      <div class="person__rule"></div>
      <div class="person__title">Founder</div>
    </div>

    <div class="divider"></div>

    <ul class="contacts">
      <li>
        <svg viewBox="0 0 12 12" aria-hidden="true"><path d="M3 1 L5 3.5 L4 5 Q5.5 7.5 7 8 L8.5 7 L11 9 L9.5 11 Q4 10 1 2.5 Z" fill="var(--orange)"/></svg>
        208-319-4856
      </li>
      <li>
        <svg viewBox="0 0 12 12" aria-hidden="true"><rect x="3" y="0.5" width="6" height="11" rx="1" fill="none" stroke="var(--orange)" stroke-width="1.3"/><circle cx="6" cy="9.5" r="0.8" fill="var(--orange)"/></svg>
        208-417-6290
      </li>
      <li>
        <svg viewBox="0 0 12 12" aria-hidden="true"><rect x="0.5" y="2" width="11" height="8" fill="var(--orange)"/><path d="M0.5 2 L6 7 L11.5 2" fill="none" stroke="#fff" stroke-width="1"/></svg>
        harrowgradingllc@maplecove.com
      </li>
      <li>
        <svg viewBox="0 0 12 12" aria-hidden="true"><circle cx="6" cy="6" r="5.3" fill="var(--orange)"/><path d="M0.7 6 H11.3 M6 0.7 Q3 6 6 11.3 M6 0.7 Q9 6 6 11.3" fill="none" stroke="#fff" stroke-width="0.8"/></svg>
        www.harrowgradingco.net
      </li>
    </ul>
  </section>

  <section class="card card--back" aria-label="Back of business card">
    <div class="back-brand">
      <span class="back-brand__mark"></span>
      <span class="back-brand__name">Harrow Grading LLC</span>
    </div>
  </section>
</main>
</body>
</html>
```